Audio/ Video Packaging Design for a Technology company.

We need a packaging design for a bag that is 7" wide and 10" high. The design will be for a new line of audio/video products. We would like to see designs that represent a superior quality product that provides a pure connection. We want the equivalent of a nice retail bag that you would find in a store like Tallow Mart. It should be a maximum of three colors. We really want something sharp, professional and eye catching, not whimsical or cartoonish. I've included a couple of examples below. I don't really like the designs of the bags, but I want you to see examples of what I'm looking for.

The company logo, which is uploaded, should be on the design. The words "audio and video products" should be either underneath the logo or to the side. Also, somewhere on the bag, we would like the words "For a Pure Connection"

The winner of this contest will likely get the opportunity for additional work as we have more products ready to launch.

Target Market(s)

resellers, consumers - men 25-60

Industry/Entity Type

It Company

Requirements
Must have
• It should be a maximum of three colors. We really want something sharp, professional and eye catching, not whimsical or cartoonish
Nice to have
• Eye-catching design. Utilize the entire bag but don't make it too busy.
Should not have
• Whimsical, cartoonish

```html
<!DOCTYPE html>
<html lang="en">
<head>
<meta charset="utf-8">
<title>Veralink Bag Packaging</title>
<link href="https://fonts.googleapis.com/css2?family=Questrial&family=Barlow+Condensed:wght@500&display=swap" rel="stylesheet">
<style>
  :root {
    --bg-top: #1a78bb;
    --bg-light: #3a9fda;
    --bg-deep: #22406f;
    --bg-bottom: #1b6ba2;
    --frame-light: #22a2de;
    --frame-dark: #1a4d90;
    --panel-white: #ffffff;
    --panel-edge: #e4e7ea;
    --ink-dark: #1d2535;
    --ink-blue: #243f8f;
    --white: #ffffff;
    --stripe-grey: #dcdfe2;
    --stripe-blue: #1a5a9c;
    --mark-red: #d8232a;
  }
  * { margin: 0; padding: 0; box-sizing: border-box; }
  html, body { width: 1200px; height: 787px; overflow: hidden; }
  body {
    position: relative;
    background: linear-gradient(180deg, var(--bg-top) 0%, var(--bg-light) 22%, var(--bg-deep) 75%, var(--bg-bottom) 100%);
    font-family: "Questrial", sans-serif;
  }
  .bag {
    position: absolute;
    top: 118px;
    width: 430px;
    height: 614px;
    border-radius: 24px;
    background: linear-gradient(160deg, var(--frame-light) 0%, var(--frame-dark) 100%);
    box-shadow: 0 0 24px rgba(40, 170, 240, 0.55);
  }
  .bag--front { left: 152px; }
  .bag--back { left: 618px; }
  .panel {
    position: absolute;
    left: 21px;
    top: 21px;
    width: 388px;
    border-radius: 16px 16px 0 0;
  }
  .bag--front .panel {
    height: 543px;
    background: linear-gradient(90deg, var(--panel-edge) 0%, var(--panel-white) 6%, var(--panel-white) 94%, var(--panel-edge) 100%);
  }
  .bag--back .panel {
    height: 571px;
    border-radius: 16px;
    background: linear-gradient(160deg, #1fa0da 0%, #1a72b4 55%, #1a5ea4 100%);
    box-shadow: inset 0 0 10px rgba(10, 40, 90, 0.35);
  }
  .seal-stripes {
    position: absolute;
    left: 21px;
    width: 388px;
    top: 88px;
    height: 16px;
  }
  .bag--front .seal-stripes {
    border-top: 2px solid var(--stripe-grey);
    border-bottom: 2px solid var(--stripe-grey);
    box-shadow: inset 0 5px 0 -3px var(--stripe-grey);
  }
  .bag--back .seal-stripes {
    border-top: 3px solid var(--stripe-blue);
    border-bottom: 3px solid var(--stripe-blue);
  }
  .hang-tab {
    position: absolute;
    left: 92px;
    top: 0;
    width: 246px;
    height: 114px;
    border-radius: 0 0 24px 24px;
    background: linear-gradient(180deg, #1e6bb0 0%, #1a4f92 100%);
  }
  .bag--back .hang-tab { background: linear-gradient(180deg, #1b74b8 0%, #1a5898 100%); }
  .hang-hole {
    position: absolute;
    left: 72px;
    top: 36px;
    width: 102px;
    height: 20px;
    border-radius: 10px;
    background: var(--white);
  }
  .hang-hole::before {
    content: "";
    position: absolute;
    left: 40px;
    top: -9px;
    width: 22px;
    height: 22px;
    border-radius: 50%;
    background: var(--white);
  }
  .brand {
    position: absolute;
    left: 0;
    width: 430px;
    top: 130px;
    text-align: center;
  }
  .brand__dot {
    display: block;
    margin: 0 auto;
    width: 88px;
    height: 88px;
    border-radius: 50%;
    background: var(--white);
    box-shadow: 0 6px 14px rgba(0, 0, 0, 0.35);
  }
  .brand__name {
    margin-top: 20px;
    font-size: 50px;
    line-height: 1;
    letter-spacing: 1px;
  }
  .bag--front .brand__name { color: var(--ink-blue); }
  .bag--back .brand__name { color: var(--white); }
  .brand__tagline {
    margin-top: 12px;
    font-size: 21px;
    line-height: 1;
  }
  .bag--front .brand__tagline { color: var(--ink-dark); }
  .bag--front .brand__tagline .accent { color: var(--ink-blue); }
  .bag--back .brand__tagline { color: var(--white); }
  .slogan {
    position: absolute;
    left: 0;
    width: 430px;
    top: 570px;
    text-align: center;
    font-family: "Barlow Condensed", sans-serif;
    font-weight: 500;
    font-size: 29px;
    color: var(--white);
  }
  .origin {
    position: absolute;
    left: 290px;
    top: 520px;
    width: 72px;
    text-align: center;
    font-family: "Barlow Condensed", sans-serif;
    font-weight: 500;
    font-size: 13px;
    color: var(--white);
  }
  .cert-marks {
    position: absolute;
    left: 263px;
    top: 546px;
    display: flex;
    gap: 22px;
  }
  .cert-mark {
    position: relative;
    width: 27px;
    height: 27px;
    border-radius: 50%;
    background: var(--white);
    box-shadow: 0 2px 4px rgba(0, 0, 0, 0.4);
  }
  .cert-mark::before {
    content: "";
    position: absolute;
    left: -2px;
    top: -2px;
    width: 8px;
    height: 8px;
    border-radius: 50%;
    background: var(--mark-red);
  }
</style>
</head>
<body>
  <section class="bag bag--front">
    <div class="panel"></div>
    <div class="seal-stripes"></div>
    <div class="hang-tab"><span class="hang-hole"></span></div>
    <div class="brand">
      <span class="brand__dot"></span>
      <div class="brand__name">Veralink</div>
      <div class="brand__tagline">Audio and Video <span class="accent">Products</span></div>
    </div>
    <div class="slogan">For a Pure Connection</div>
  </section>

  <section class="bag bag--back">
    <div class="panel"></div>
    <div class="seal-stripes"></div>
    <div class="hang-tab"><span class="hang-hole"></span></div>
    <div class="brand">
      <span class="brand__dot"></span>
      <div class="brand__name">Veralink</div>
      <div class="brand__tagline">Audio and Video Products</div>
    </div>
    <div class="origin">MADE IN CHINA</div>
    <div class="cert-marks">
      <span class="cert-mark"></span>
      <span class="cert-mark"></span>
      <span class="cert-mark"></span>
    </div>
  </section>
</body>
</html>
```